Hello my name is Colin, I am Starting a business called Lumen Wellness and fitness and am in need of a memorable business card.
It is a personal training studio. I have added the logo that i would like to be on the left center om my business card. i would like room left up the top for a heading sentence such as. "Is your body shocking for all the wrong reasons". there must be room left on the right of the logo below the main heading for 3 sub headings.
then under those 3 headings and logo room for another larger heading eg. "give me a call and learn how to eat chocolate, drink bear and have great sex". in what room is left i would like to be used for my contact details, use I'm Colin Ferrante your fitness expert on the left then on the right Phone, Email and website space in at least 12 Point. Very specific i know :) now onto the back, for the back i would like an eye catching graphic and room for one main headline and 3 bullet points centered just write anything i will choose what to put in them when i pick a winner. Thank you very much for sticking through all of that :) i appreciate you taking the time to read it and hopefully undergo designing me a business card.
I can't wait to see the designs!

Target Market(s)

slightly more towards females although it would probably be best if it was targeted towards both sexes

Industry/Entity Type

Training

Requirements
Nice to have
• I would love to see if anyone could come up with a design that would really make my card stand out and be memorable.
Should not have
• tacky fitness photos of abs and muscles etc.

```html
<!DOCTYPE html>
<html lang="en">
<head>
<meta charset="utf-8">
<title>Lumen Wellness and Fitness – Business Card</title>
<link href="https://fonts.googleapis.com/css2?family=Questrial&family=Open+Sans:wght@400&display=swap" rel="stylesheet">
<style>
  :root {
    --backdrop: #6a4326;
    --card: #ffffff;
    --ink: #333333;
    --brand: #1b4f8c;
    --brand-deep: #0f2f5c;
    --brand-light: #1d5ca6;
    --band-dark: #323232;
    --label: #1a1a1a;
    --white: #ffffff;
  }
  * { box-sizing: border-box; margin: 0; padding: 0; }
  html, body { width: 1200px; height: 788px; overflow: hidden; }
  body {
    position: relative;
    background: var(--backdrop);
    font-family: "Questrial", "Century Gothic", sans-serif;
    color: var(--ink);
  }
  .side-label {
    position: absolute;
    font-family: "Open Sans", Arial, sans-serif;
    font-size: 21px;
    color: var(--label);
  }
  .card {
    position: absolute;
    width: 524px;
    height: 300px;
    background: var(--card);
    border-radius: 22px;
    overflow: hidden;
    box-shadow: 0 6px 14px rgba(0,0,0,0.35);
  }
  .card-front { left: 338px; top: 78px; }
  .card-back-one { left: 54px; top: 445px; }
  .card-back-two { left: 621px; top: 441px; }

  .headline {
    position: absolute;
    left: 0; right: 0;
    text-align: center;
    font-size: 13px;
    color: var(--ink);
  }
  .wordmark {
    position: absolute;
    color: var(--brand);
    font-family: "Questrial", "Century Gothic", sans-serif;
    line-height: 1;
    text-align: right;
  }
  .wordmark .name { display: block; }
  .wordmark .sub { display: block; }

  /* Front */
  .card-front .headline { top: 24px; }
  .card-front .wordmark { left: 136px; top: 56px; width: 250px; }
  .card-front .wordmark .name { font-size: 68px; letter-spacing: 1px; }
  .card-front .wordmark .sub { font-size: 19px; margin-top: 4px; }
  .offer-band {
    position: absolute;
    left: 0; right: 0; top: 166px; height: 34px;
    background: var(--band-dark);
    color: var(--white);
    font-size: 13px;
    text-align: center;
    line-height: 34px;
  }
  .contact-band {
    position: absolute;
    left: 0; right: 0; top: 206px; bottom: 0;
    background: linear-gradient(90deg, var(--brand-light), var(--brand-deep));
    color: var(--white);
  }
  .contact-person {
    position: absolute;
    right: 279px; top: 28px;
    text-align: right;
  }
  .contact-person .person-name { font-size: 17px; }
  .contact-person .person-role { font-size: 13px; margin-top: 3px; }
  .contact-divider {
    position: absolute;
    left: 254px; top: 18px; width: 1px; height: 60px;
    background: var(--white);
  }
  .contact-list {
    position: absolute;
    left: 264px; top: 10px;
    list-style: none;
    font-size: 19px;
    line-height: 24px;
  }
  .contact-list b { font-style: italic; display: inline-block; width: 16px; }

  /* Back 1 */
  .figure-art {
    position: absolute;
    left: 40px; top: 20px; width: 150px; height: 262px;
    background: linear-gradient(180deg, var(--brand-light), var(--brand-deep));
    border-radius: 60px 60px 10px 10px;
    opacity: 0.9;
  }
  .card-back-one .wordmark { left: 254px; top: 24px; width: 126px; }
  .card-back-one .wordmark .name { font-size: 36px; }
  .card-back-one .wordmark .sub { font-size: 10px; margin-top: 2px; }
  .point-list {
    position: absolute;
    left: 258px; top: 116px;
    list-style: none;
    font-family: "Open Sans", Arial, sans-serif;
    font-size: 16px;
    color: var(--label);
  }
  .point-list li { height: 34px; position: relative; padding-left: 25px; }
  .point-list li::before {
    content: ""; position: absolute; left: 0; top: 8px;
    width: 6px; height: 6px; background: var(--label);
  }
  .card-back-one .site {
    position: absolute; left: 256px; top: 254px;
    font-family: "Open Sans", Arial, sans-serif;
    font-size: 19px; color: var(--ink);
  }

  /* Back 2 */
  .card-back-two .headline { top: 20px; }
  .card-back-two .wordmark { left: 102px; top: 88px; width: 320px; }
  .card-back-two .wordmark .name { font-size: 92px; letter-spacing: 1px; }
  .card-back-two .wordmark .sub { font-size: 23px; margin-top: 4px; }
  .card-back-two .site {
    position: absolute; left: 0; right: 0; top: 252px;
    text-align: center;
    font-size: 20px; letter-spacing: 4px; color: var(--ink);
  }
</style>
</head>
<body>
  <div class="side-label" style="left:572px; top:33px;">Front</div>
  <div class="side-label" style="left:284px; top:403px;">Back - 1</div>
  <div class="side-label" style="left:857px; top:403px;">Back - 2</div>

  <section class="card card-front">
    <p class="headline">Is your body shocking for all the wrong reasons</p>
    <div class="wordmark">
      <span class="name">Lumen</span>
      <span class="sub">Wellness and Fitness</span>
    </div>
    <div class="offer-band">Give me a call and learn how to eat chocolate drink bear and have great sex</div>
    <div class="contact-band">
      <div class="contact-person">
        <p class="person-name">Colin Ferrante</p>
        <p class="person-role">Your Fitness Expert</p>
      </div>
      <div class="contact-divider"></div>
      <ul class="contact-list">
        <li><b>p</b> : +12 345 67890</li>
        <li><b>e</b> : info@website.com</li>
        <li><b>w</b> : www.website.com</li>
      </ul>
    </div>
  </section>

  <section class="card card-back-one">
    <div class="figure-art" role="img" aria-label="Blue silhouette illustration of a man in a suit standing beside a tall woman"></div>
    <div class="wordmark">
      <span class="name">Lumen</span>
      <span class="sub">Wellness and Fitness</span>
    </div>
    <ul class="point-list">
      <li>Lorem Ipsum has been ...</li>
      <li>Lorem Ipsum has been ...</li>
      <li>Lorem Ipsum has been ...</li>
    </ul>
    <p class="site">www.website.com</p>
  </section>

  <section class="card card-back-two">
    <p class="headline">Is your body shocking for all the wrong reasons</p>
    <div class="wordmark">
      <span class="name">Lumen</span>
      <span class="sub">Wellness and Fitness</span>
    </div>
    <p class="site">www.website.com</p>
  </section>
</body>
</html>
```